Catering Menu Package

I currently have a complete menu package, which we have redesigned as far as content, now I need to it put together in a catalog type format. It is essentially 10-12 pages in length, and will be sent for print production. Upon receiving a final edit
Updates

I have added an example gif to the project.

I did this free hand this basically what I am looking for. please change text and type to whatever you think would look best. This is a total rough design so, feel free to change any and everything. The text for the page is on the word documents. If you need more images let me know I am in the process of getting as many images uploaded for your use.

Project Deadline Extended
Reason: I figured we got a late jump with questions, so i am extending a few days .

Target Market(s)

The target market is business who wish to have catered luncheons, breakfasts , meetings

Industry/Entity Type

Catering

Requirements
Must have
• I have attached a copy of the text that what we want in the package, our logo, and i have also attached a catering package of another company to give you an idea what the finished product will be
Should not have
• It should not look identical to the example catering packages, these are for some inspiration we want our own design with the same type of look and feel

```html
<!DOCTYPE html>
<html lang="en">
<head>
<meta charset="utf-8">
<title>Breakfast Menu – Meadowbrook Country Caterers</title>
<link rel="stylesheet" href="https://fonts.googleapis.com/css2?family=Parisienne&family=Lora:wght@400&display=swap">
<style>
  :root {
    --page-bg-start: #ffffff;
    --page-bg-end: #ebe8e5;
    --band-top: #ffffff;
    --band-bottom: #dccbbd;
    --heading: #5b3317;
    --item: #5c4a40;
    --brand: #1c1c1c;
    --brand-accent: #d9622b;
  }
  * { box-sizing: border-box; margin: 0; padding: 0; }
  html, body { width: 1200px; height: 927px; overflow: hidden; }
  body {
    position: relative;
    background: linear-gradient(100deg, var(--page-bg-start) 35%, var(--page-bg-end) 100%);
    font-family: "Lora", Georgia, serif;
  }
  .side-band {
    position: absolute; left: 0; top: 0; width: 182px; height: 927px;
    background: linear-gradient(180deg, var(--band-top) 30%, var(--band-bottom) 100%);
  }
  .brand {
    position: absolute; left: 27px; top: 40px; width: 135px;
    display: flex; flex-direction: column; align-items: center; gap: 14px;
  }
  .brand-mark {
    width: 70px; height: 70px; border-radius: 50%;
    background: var(--brand-accent);
  }
  .brand-name {
    font-family: "Lora", Georgia, serif; font-size: 19px; line-height: 1.2;
    color: var(--brand); text-align: center;
  }
  .section-title {
    position: absolute;
    font-family: "Parisienne", cursive;
    font-size: 36px; font-weight: 400; color: var(--heading);
    white-space: nowrap; line-height: 1;
  }
  .menu-list {
    position: absolute; list-style: none;
    font-size: 16.5px; color: var(--item); line-height: 1.3;
  }
  .menu-list li { position: absolute; white-space: nowrap; }
  .align-right { text-align: right; }
  .align-right li { right: 0; }
  .align-left li { left: 0; }
  .photo { position: absolute; }
  .photo-strata {
    left: 665px; top: 39px; width: 402px; height: 237px;
    background: linear-gradient(135deg, #7d7c77 0%, #b59b6a 40%, #e9e6e0 65%, #8a2b2e 100%);
  }
  .photo-pancakes {
    left: 315px; top: 327px; width: 349px; height: 215px;
    background: radial-gradient(circle at 45% 40%, #e2a874 0%, #b96434 45%, #7a3513 100%);
  }
  .photo-coffee {
    left: 665px; top: 611px; width: 291px; height: 271px;
    background: radial-gradient(circle at 55% 70%, #efe6da 0%, #b08f6a 45%, #5f3c22 100%);
  }
</style>
</head>
<body>
  <div class="side-band"></div>

  <div class="brand">
    <span class="brand-mark"></span>
    <span class="brand-name">Meadowbrook Country Caterers</span>
  </div>

  <h2 class="section-title" style="right:588px; top:52px;">Breakfast Stratas</h2>
  <ul class="menu-list align-right" style="left:0; width:612px; top:0;">
    <li style="top:121px;">Breakfast Stratas (Serves 10-12 people)</li>
    <li style="top:157px;">French Toast Strata</li>
    <li style="top:194px;">Redskin Potato &amp; Maple Sausage Strata</li>
    <li style="top:230px;">Twice Baked Breakfast Potato Casserole</li>
  </ul>
  <div class="photo photo-strata" role="img" aria-label="Slice of breakfast strata with spinach and tomato on a white plate beside a red napkin and fork"></div>

  <div class="photo photo-pancakes" role="img" aria-label="Stack of buttermilk pancakes topped with whipped butter and maple syrup"></div>
  <h2 class="section-title" style="left:689px; top:330px;">Ala Carte Breakfast Items</h2>
  <ul class="menu-list align-left" style="left:689px; width:420px; top:0;">
    <li style="top:395px; white-space:normal; width:410px;">Buttermilk Pancakes served with Warm Maple Syrup &amp; Whipped Butter</li>
    <li style="top:452px;">Redskin Potato Hash Browns</li>
    <li style="top:489px;">Maple Sausage Links</li>
    <li style="top:525px;">Applewood Smoked Bacon</li>
  </ul>

  <h2 class="section-title" style="right:588px; top:582px;">Breakfast Beverages</h2>
  <ul class="menu-list align-right" style="left:0; width:612px; top:0;">
    <li style="top:645px;">Fresh Squeezed Orange Juice</li>
    <li style="top:681px;">Cranberry Juice</li>
    <li style="top:718px;">Apple Juice</li>
    <li style="top:754px;">Bottled Water</li>
    <li style="top:790px;">Bottled Juices</li>
    <li style="top:827px;">Hearthside Select Gourmet Coffee Station</li>
    <li style="top:863px;">Hot Tea</li>
  </ul>
  <div class="photo photo-coffee" role="img" aria-label="Steaming cup of black coffee on a saucer with cinnamon sticks"></div>
</body>
</html>
```